Velvet Riot Rising Line of Sparkling Wine & Spirits

Back info: Nora Beth Quill Owner 555-318-4402 1480 E. Harlow Ave, Bldg. 2, & 3, Lodi Ca. 95871
Sparkling Wines & Memorabilia www.velvetriotrising.com
Ok I have uploaded the winning design. The color that I am after is the Fushia, Raspberry, Red, Matte Satin Matalic Finish. With a 24 Karet Gold color Foil. The Bottle is on the top row and it's the 2nd Bottle in. That is the Color that I want. This is the style of font. Make sure that you put what we're advertising. Good Luck to you all. Warmest regards, Nora
21 & up UniSex
Sparkling Wine and Memorabilia
there listed up above.....

```html
<!DOCTYPE html>
<html lang="en">
<head>
<meta charset="utf-8">
<title>Velvet Riot Rising — Business Card</title>
<link href="https://fonts.googleapis.com/css2?family=Arimo:wght@400;700&display=swap" rel="stylesheet">
<style>
  :root {
    --page: #dcdcdc;
    --card: #ffffff;
    --fuchsia: #d0157a;
    --fuchsia-deep: #a50f5f;
    --fuchsia-light: #e8459c;
    --gold: #e6a83a;
    --ink: #444444;
    --ink-dark: #1a1a1a;
    --fade-grey: #5a5a5a;
  }
  * { margin: 0; padding: 0; box-sizing: border-box; }
  html, body { width: 1200px; height: 1200px; overflow: hidden; }
  body {
    background: var(--page);
    font-family: "Arimo", Arial, sans-serif;
    position: relative;
  }
  .card {
    position: absolute;
    left: 256px;
    width: 688px;
    height: 394px;
    background: var(--card);
    overflow: hidden;
  }
  .card-front { top: 159px; }
  .card-back { top: 654px; }

  .bottle-art {
    position: absolute;
    border-radius: 10px 10px 6px 6px;
    background: linear-gradient(90deg, var(--fuchsia-deep), var(--fuchsia-light) 45%, var(--fuchsia) 70%, var(--fuchsia-deep));
  }
  .card-front .bottle-art { left: 42px; top: 27px; width: 50px; height: 163px; }
  .card-back .bottle-art { left: 308px; top: 57px; width: 71px; height: 243px; z-index: 2; }

  .holder-name {
    position: absolute; left: 44px; top: 208px;
    font-weight: 700; font-size: 28px; color: var(--fuchsia);
    letter-spacing: 0.2px;
  }
  .holder-role {
    position: absolute; left: 44px; top: 242px;
    font-size: 17px; color: var(--gold);
  }
  .address {
    position: absolute; left: 44px; top: 277px;
    font-size: 16.5px; line-height: 21px; color: var(--ink);
  }
  .contact {
    position: absolute; left: 44px; top: 327px;
    list-style: none; font-size: 16.5px; line-height: 20px; color: var(--ink);
  }
  .contact li { display: flex; align-items: center; gap: 11px; }
  .contact svg { width: 15px; height: 15px; flex: none; }

  .back-fade {
    position: absolute; left: 0; right: 0; top: 182px; bottom: 0;
    background: linear-gradient(180deg, #ffffff 0%, #cfcfcf 35%, #8a8a8a 75%, var(--fade-grey) 100%);
  }
  .ground-line {
    position: absolute; left: 149px; width: 401px; top: 299px; height: 1px;
    background: linear-gradient(90deg, transparent, #333 25%, #333 75%, transparent);
  }
  .tagline {
    position: absolute; left: 0; right: 0; top: 326px;
    text-align: center; font-size: 17px; letter-spacing: 4.6px;
    color: var(--ink-dark);
  }
  .tagline strong { font-weight: 700; }
</style>
</head>
<body>
  <section class="card card-front">
    <div class="bottle-art" role="img" aria-label="Fuchsia sparkling wine bottle with gold foil and brand label"></div>
    <h1 class="holder-name">NORA BETH QUILL</h1>
    <p class="holder-role">Owner</p>
    <p class="address">E. Harlow Ave<br>Bldg. 2, &amp; 3, Lodi Ca. 95871</p>
    <ul class="contact">
      <li>
        <svg viewBox="0 0 24 24" aria-hidden="true"><path fill="#d0157a" d="M6.6 10.8c1.4 2.8 3.8 5.1 6.6 6.6l2.2-2.2c.3-.3.7-.4 1-.2 1.1.4 2.3.6 3.6.6.6 0 1 .4 1 1V20c0 .6-.4 1-1 1C10.6 21 3 13.4 3 4c0-.6.4-1 1-1h3.5c.6 0 1 .4 1 1 0 1.3.2 2.5.6 3.6.1.3 0 .7-.2 1L6.6 10.8z"/></svg>
        <span>555-318-4402 1480</span>
      </li>
      <li>
        <svg viewBox="0 0 24 24" aria-hidden="true"><circle cx="12" cy="12" r="10" fill="#d0157a"/><path fill="#fff" d="M7 6c2 1 3 3 2 5s-3 1-3 3 2 3 1 5c-2-1-4-4-4-7 0-2 1-4 4-6zm8 2c2 0 3 2 2 3s-3 0-3 2 2 2 1 4-3 1-3-1 2-2 1-4 0-4 2-4z"/></svg>
        <span>www.velvetriotrising.com</span>
      </li>
    </ul>
  </section>

  <section class="card card-back">
    <div class="back-fade"></div>
    <div class="ground-line"></div>
    <div class="bottle-art" role="img" aria-label="Fuchsia sparkling wine bottle with gold foil and brand label"></div>
    <p class="tagline">SPARKLING <strong>WINES &amp; MEMORABILIA</strong></p>
  </section>
</body>
</html>
```